Climbing Gear Company Stationary Design

We need some new stationary to standardise our business.
We require:

Business Card
A4 Letterhead
With complements slip

Our business is a Distributor and retailer of rock climbing equipment throughout Australia.
We need to the stationary (business card in particular) to reflect this.

Target Market(s)

customers, other retail outlets, overseas manufacturers.

Industry/Entity Type

Business

Requirements
Must have
• company logo
website url- www.ridgetopgearworks.com.au
email - mark@ridgetopgearworks.com
Business Address: Unit 3, 14-16 Marlowe Street, Kestrel Vale, Eastmark, 2371
Phone: 0438 627 194
my Name (on Business card) - Gordon Pellimore
use of Blue colour in our logo

```html
<!DOCTYPE html>
<html lang="en">
<head>
<meta charset="utf-8">
<title>Ridgetop Gearworks – Business Card</title>
<link rel="stylesheet" href="https://fonts.googleapis.com/css2?family=Open+Sans:wght@400;600;700;800&display=swap">
<style>
  :root {
    --brand-blue: #1f5e9c;
    --card-blue: #2366a3;
    --card-white: #f7f7f7;
    --ink-grey: #6a6a6a;
    --name-grey: #555555;
    --backdrop: #ddd6cc;
  }
  * { margin: 0; padding: 0; box-sizing: border-box; }
  html, body {
    width: 1200px;
    height: 407px;
    overflow: hidden;
    background: var(--backdrop);
    font-family: "Open Sans", Arial, sans-serif;
  }
  .stage {
    position: relative;
    width: 1200px;
    height: 407px;
  }
  .card {
    position: absolute;
    top: 60px;
    width: 504px;
    height: 288px;
    box-shadow: 3px 4px 6px rgba(0,0,0,0.35);
  }
  .card--front {
    left: 60px;
    background: radial-gradient(ellipse at 45% 35%, #ffffff 0%, var(--card-white) 60%, #e9e9e9 100%);
  }
  .card--back {
    left: 636px;
    background: var(--card-blue);
  }
  .brand-name {
    position: absolute;
    font-weight: 800;
    font-size: 32px;
    letter-spacing: 0.5px;
    white-space: nowrap;
    line-height: 1;
  }
  .tagline {
    position: absolute;
    font-weight: 600;
    font-size: 15px;
    letter-spacing: 2.8px;
    white-space: nowrap;
    line-height: 1;
  }
  .card--front .brand-name { left: 56px; top: 47px; color: var(--brand-blue); }
  .card--front .tagline { left: 58px; top: 89px; color: var(--brand-blue); }
  .card--back .brand-name,
  .card--back .tagline {
    left: 0; right: 0; text-align: center; color: #ffffff;
  }
  .card--back .brand-name { top: 102px; }
  .card--back .tagline { top: 144px; }

  .address, .contact {
    position: absolute;
    left: 23px;
    font-size: 12.5px;
    line-height: 19.5px;
    color: var(--ink-grey);
    font-style: normal;
  }
  .address { top: 158px; }
  .contact { top: 212px; }
  .holder-name {
    position: absolute;
    right: 26px;
    top: 250px;
    font-size: 16px;
    font-weight: 700;
    color: var(--name-grey);
  }
  .web-address {
    position: absolute;
    left: 0; right: 0;
    top: 255px;
    text-align: center;
    color: #ffffff;
    font-size: 14px;
    letter-spacing: 2px;
  }
</style>
</head>
<body>
<main class="stage">
  <section class="card card--front" aria-label="Business card front">
    <div class="brand-name">RIDGETOP GEARWORKS</div>
    <div class="tagline">OUR KIT•YOUR CLIMB•THE HIGH LIFE</div>
    <address class="address">
      Unit 3, 14-16 Marlowe Street,<br>
      Kestrel Vale, Eastmark, 2371
    </address>
    <div class="contact">
      P : 0438 627 194<br>
      E : mark@ridgetopgearworks.com<br>
      W: www.ridgetopgearworks.com
    </div>
    <div class="holder-name">Gordon Pellimore</div>
  </section>

  <section class="card card--back" aria-label="Business card back">
    <div class="brand-name">RIDGETOP GEARWORKS</div>
    <div class="tagline">OUR KIT•YOUR CLIMB•THE HIGH LIFE</div>
    <div class="web-address">www.ridgetopgearworks.com</div>
  </section>
</main>
</body>
</html>
```